DJ Colm Vetter

I'm looking for a professional but still artsy/progressive design. I come from a hip hop/club DJ background playing a lot of underground music but have switched to doing more corporate parties and weddings recently. I am all about keeping the dancefloor moving and emotionally connecting with the crowd. I'd like a trendy/updated color palette. Something that's clean enough that looks professional but also trendy enough to convey that by the end of the night we'll be sweatily dancing to the latest hits. Some designers/artists I like: Tarn Olquist, Pavel Remy, Wendell Quarrie, Lumeno 7400, Silas Dravin.

```html
<!DOCTYPE html>
<html lang="en">
<head>
<meta charset="UTF-8">
<title>DJ Colm Vetter – Business Card</title>
<link href="https://fonts.googleapis.com/css2?family=Bebas+Neue&family=Lato:wght@400;700&display=swap" rel="stylesheet">
<style>
  :root {
    --backdrop: #8a4f1f;
    --card: #231f20;
    --accent: #ece331;
    --ink: #ffffff;
    --rule: #6b6869;
  }
  * { margin: 0; padding: 0; box-sizing: border-box; }
  html, body {
    width: 1200px;
    height: 900px;
    overflow: hidden;
    background: var(--backdrop);
  }
  .stage { position: relative; width: 1200px; height: 900px; }
  .card {
    position: absolute;
    left: 330px;
    width: 557px;
    height: 343px;
    background: var(--card);
    box-shadow: 3px 4px 6px rgba(0, 0, 0, 0.45);
  }
  .card--contact { top: 90px; }
  .card--brand { top: 470px; }

  .contact {
    position: absolute;
    left: 0; right: 0; top: 60px;
    text-align: center;
    font-family: "Lato", sans-serif;
    color: var(--ink);
    font-size: 16px;
    line-height: 20px;
  }
  .contact__name {
    font-family: "Bebas Neue", sans-serif;
    color: var(--accent);
    font-size: 29px;
    line-height: 30px;
    letter-spacing: 0.3px;
  }
  .contact__role { margin-top: 0; }
  .contact__rule {
    width: 125px;
    height: 1px;
    background: var(--rule);
    margin: 12px auto 12px;
  }
  .contact__label { color: var(--accent); font-weight: 700; }
  .contact__address { margin-top: 0; }

  .brand {
    position: absolute;
    left: 0; right: 0; top: 132px;
    display: flex;
    align-items: center;
    justify-content: center;
    gap: 16px;
  }
  .brand__mark {
    width: 22px;
    height: 22px;
    background: var(--accent);
  }
  .brand__name {
    font-family: "Bebas Neue", sans-serif;
    color: var(--ink);
    font-size: 76px;
    line-height: 80px;
    letter-spacing: 0.5px;
  }
</style>
</head>
<body>
<main class="stage">
  <section class="card card--contact">
    <div class="contact">
      <h1 class="contact__name">Colm Vetter</h1>
      <p class="contact__role">Managing Director</p>
      <div class="contact__rule"></div>
      <p><span class="contact__label">P:</span> 031-482 617 905</p>
      <p><span class="contact__label">M:</span> 031-482 617 905</p>
      <p><span class="contact__label">E:</span> hello@colmvetter.com</p>
      <p><span class="contact__label">W:</span> www.colmvetter.com</p>
      <div class="contact__rule"></div>
      <p class="contact__address">48 Harbour Lane, Studio 3<br>Eastbridge, 720415.</p>
    </div>
  </section>

  <section class="card card--brand">
    <div class="brand">
      <span class="brand__mark"></span>
      <h2 class="brand__name">DJ Colm Vetter</h2>
    </div>
  </section>
</main>
</body>
</html>
```